Stylish Business Cards Wanted

- DOUBLE SIDED Design Required -

High end, edgy cards for a corporate and personal stylist. Must include logo,
Name: Belinda Harwick
Title: Director and Stylist
telephone : +61 8 7142 5809
email: belinda@theloombriefing.example
website: theloombriefing.example
Tag: Corporate Workwear & Uniform Specialist | Personal Stylist
Would like nice icons for telephone, email, website

Target Market(s)

Businesses wanting stylish uniforms, people wanting stylish wardrobes

Industry/Entity Type

Corporate Workwear Stylist

Contact Information for Business Card

I would like black, white and gold foiling incorporated in the design - possibly a touch of the other colours on my branding guide attached Name: Belinda Harwick Title: Director and Stylist telephone : +61 8 7142 5809 email: belinda@theloombriefing.example website: theloombriefing.example Tag: Corporate Workwear & Uniform Specialist | Personal Stylist Would like nice icons for telephone, email, website

Font styles to use
Other font styles liked:
• Raleway

Colors

Designer to choose colors to be used in the design.

Requirements
Must have
• Gold foil accents

```html
<!DOCTYPE html>
<html lang="en">
<head>
<meta charset="utf-8">
<title>The Loom Briefing — Business Cards</title>
<link rel="stylesheet" href="https://fonts.googleapis.com/css2?family=Dancing+Script:wght@600&family=Roboto:wght@400;500&display=swap">
<style>
  :root {
    --navy: #151c30;
    --gold: #d9ac4c;
    --gold-light: #e8c46a;
    --paper: #f6f6f4;
    --ink: #1b1f2a;
    --backdrop: #c9c9c9;
  }
  * { box-sizing: border-box; margin: 0; padding: 0; }
  html, body {
    width: 1200px; height: 852px; overflow: hidden;
    background: var(--backdrop);
  }
  .sheet {
    position: relative; width: 1200px; height: 852px;
    display: flex; align-items: center; justify-content: center; gap: 40px;
  }
  .card {
    position: relative; width: 540px; height: 310px;
    border-radius: 22px; overflow: hidden;
  }
  /* Back of card */
  .card--back {
    background: var(--navy);
    display: flex; align-items: center; justify-content: center;
  }
  .brand-name {
    font-family: "Dancing Script", cursive;
    font-weight: 600;
    line-height: 1;
    text-align: center;
  }
  .card--back .brand-name { color: var(--gold); font-size: 58px; }

  /* Front of card */
  .card--front { background: var(--paper); }
  .front-wave { position: absolute; inset: 0; width: 100%; height: 100%; }
  .tagline {
    position: absolute; top: 16px; right: 28px;
    font-family: "Dancing Script", cursive; font-weight: 600;
    color: #fff; font-size: 14px; line-height: 1.15; text-align: right;
  }
  .card--front .brand-name {
    position: absolute; right: 36px; top: 156px; width: 170px;
    color: var(--navy); font-size: 40px;
  }
  .holder { position: absolute; left: 34px; top: 182px; }
  .holder-name {
    font-family: "Dancing Script", cursive; font-weight: 600;
    color: var(--gold); font-size: 28px; line-height: 1;
  }
  .holder-title {
    font-family: "Roboto", sans-serif; font-size: 12px; color: var(--ink);
    margin-top: 4px;
  }
  .contacts {
    position: absolute; left: 34px; top: 234px; list-style: none;
    font-family: "Roboto", sans-serif; font-size: 12.5px; color: var(--ink);
  }
  .contacts li { display: flex; align-items: center; gap: 8px; height: 16px; }
  .contact-icon { width: 12px; height: 12px; flex: none; }
  .social-dot { width: 11px; height: 11px; border-radius: 50%; background: var(--gold); flex: none; margin: 0 0.5px; }
</style>
</head>
<body>
<main class="sheet">

  <section class="card card--back" aria-label="Card back">
    <p class="brand-name">The Loom Briefing</p>
  </section>

  <section class="card card--front" aria-label="Card front">
    <svg class="front-wave" viewBox="0 0 540 310" aria-hidden="true">
      <path d="M0 0 H540 V84 C470 90 400 102 320 124 C230 150 110 126 0 150 Z" fill="var(--navy)"/>
      <path d="M540 90 C470 96 400 108 320 130 C236 154 150 136 80 144" fill="none" stroke="var(--gold)" stroke-width="4" stroke-linecap="round"/>
      <path d="M0 168 C40 140 110 126 200 130 C130 134 60 150 0 180 Z" fill="var(--gold)"/>
      <path d="M20 158 C70 138 140 128 210 131" fill="none" stroke="var(--gold-light)" stroke-width="1.5"/>
    </svg>

    <p class="tagline">Corporate Workwear<br>and Uniform Specialist<br>Personal Stylist</p>

    <p class="brand-name">The Loom Briefing</p>

    <div class="holder">
      <h1 class="holder-name">Belinda Harwick</h1>
      <p class="holder-title">Director and Stylist</p>
    </div>

    <ul class="contacts">
      <li><span class="social-dot"></span>/theloombriefing101</li>
      <li>
        <svg class="contact-icon" viewBox="0 0 12 12"><circle cx="6" cy="6" r="6" fill="var(--gold)"/><path d="M3.8 3 L5 3.2 L5.3 4.6 L4.6 5.2 C5 6 5.8 6.9 6.8 7.4 L7.4 6.7 L8.8 7 L9 8.2 C8.4 8.9 7.6 9 6.6 8.5 C5 7.7 4 6.6 3.4 5 C3.1 4.1 3.2 3.5 3.8 3 Z" fill="#fff"/></svg>
        +61 8 7142 5809
      </li>
      <li>
        <svg class="contact-icon" viewBox="0 0 12 12"><rect x="0.7" y="2" width="10.6" height="8" rx="1" fill="none" stroke="var(--gold)" stroke-width="1.2"/><path d="M1 2.5 L6 6.5 L11 2.5" fill="none" stroke="var(--gold)" stroke-width="1.2"/></svg>
        belinda@theloombriefing.example
      </li>
      <li>
        <svg class="contact-icon" viewBox="0 0 12 12"><circle cx="6" cy="6" r="6" fill="var(--gold)"/><g fill="none" stroke="#fff" stroke-width="0.8"><circle cx="6" cy="6" r="4"/><ellipse cx="6" cy="6" rx="1.8" ry="4"/><path d="M2 6 H10"/></g></svg>
        theloombriefing.example
      </li>
    </ul>
  </section>

</main>
</body>
</html>
```